Social Media App Needs PPT Template

We need a PowerPoint template for a new social media company based in the DC area called "Bold Ledger." We provide an interactive digital platform for executives to share actionable advice. We would like to see designs that use our orange logo color as an accent, but are mainly grey, white, and black. The final design should communicate clean, chic, modern, and professional.

Target Market(s)

Executives

Industry/Entity Type

Information Technology

Font styles to use
Sans Serif

Colors
f78f20
fbe7d2
ffffff
000000
e8e8e8
757575

Requirements
Must have
• My project must have title page and many options for the body of the ppt (graphs, tables, etc). It also needs to be easy to modify. I must have someone who is experienced in creating powerpoint templates.
Nice to have
• It would be nice to have a very modern and clean design that includes the logo on every page, but still leaves a lot of room for the content of the slide
Should not have
• My design project should not look to busy.

```html
<!DOCTYPE html>
<html lang="en">
<head>
<meta charset="utf-8">
<title>Bold Ledger – Presentation Template</title>
<link href="https://fonts.googleapis.com/css2?family=Lato:ital,wght@0,300;0,400;0,700;1,400&display=swap" rel="stylesheet">
<style>
:root{
  --orange:#f78f20;
  --peach:#fbe7d2;
  --white:#ffffff;
  --black:#000000;
  --ink:#1f2633;
  --light:#e8e8e8;
  --paper:#f4f4f4;
  --grey:#757575;
  --mid:#9a9a9a;
  --board:#484848;
  --rule:#5a5a5a;
}
*{box-sizing:border-box;margin:0;padding:0}
html,body{width:1200px;height:722px;overflow:hidden;background:var(--board);font-family:'Lato',sans-serif}
.board{position:relative;width:1200px;height:722px}
.divider-v{position:absolute;top:0;width:1px;height:722px;background:var(--rule)}
.divider-h{position:absolute;left:0;height:1px;width:1200px;background:var(--rule)}
.page-label{position:absolute;width:243px;text-align:center;font-size:7px;color:#c4c4c4;letter-spacing:.2px}
.slide{position:absolute;width:243px;height:182px;background:var(--paper);overflow:hidden;color:var(--grey)}
.c1{left:27px}.c2{left:326px}.c3{left:626px}.c4{left:927px}
.r1{top:33px}.r2{top:274px}.r3{top:514px}
.abs{position:absolute}

/* header band */
.head{position:absolute;top:11px;left:0;width:243px;height:23px;background:var(--white)}
.head-orange{position:absolute;inset:0;background:var(--orange);clip-path:polygon(0 0,79% 0,73% 100%,0 100%)}
.head-dark{position:absolute;inset:0;background:var(--ink);clip-path:polygon(80.5% 0,84% 0,78% 100%,74.5% 100%)}
.head-line{position:absolute;top:0;right:0;width:18%;height:2px;background:var(--ink)}
.head-title{position:absolute;left:8px;top:6px;font-size:9.5px;font-weight:300;color:var(--white)}
.brand{position:absolute;display:flex;align-items:center;gap:2px;color:var(--ink);font-weight:700;white-space:nowrap}
.brand-dot{border-radius:50%;background:var(--orange)}
.head .brand{right:6px;top:7px;font-size:7px}
.head .brand-dot{width:7px;height:7px}

/* footer */
.foot{position:absolute;left:0;bottom:0;width:243px;height:9px}
.foot-band{position:absolute;right:0;bottom:0;width:100%;height:4px;background:var(--orange);clip-path:polygon(28% 0,100% 0,100% 100%,26% 100%)}
.foot-text{position:absolute;left:7px;bottom:1px;font-size:3px;color:var(--grey)}

.copy{font-size:3.6px;line-height:1.45;color:var(--grey);text-align:justify}
.lead{font-size:3.8px;line-height:1.4;color:var(--orange);font-style:italic;font-weight:700}
.photo{position:absolute}

/* title slide */
.title-brand{left:20px;top:22px;font-size:13px}
.title-brand .brand-dot{width:13px;height:13px}
.tagline{position:absolute;right:9px;bottom:16px;text-align:right;font-size:9px;font-weight:300;line-height:1.25}
.tagline .accent{color:var(--orange)}
.tagline .plain{color:var(--white)}
.transition-title{position:absolute;right:20px;bottom:15px;font-size:13px;font-weight:300;color:var(--white)}

/* lists */
.bullets{position:absolute;left:133px;top:55px;width:102px;list-style:none}
.bullets li{position:relative;padding-left:7px;font-size:3.6px;line-height:1.45;color:var(--grey);margin-bottom:6px}
.bullets li::before{content:"";position:absolute;left:0;top:1.5px;width:2.5px;height:2.5px;background:var(--orange)}

/* three column features */
.feature{position:absolute;top:50px;width:64px;text-align:center}
.feature .copy{text-align:center;margin-top:10px}

/* legend */
.legend{position:absolute;font-size:3.6px;line-height:1.5;color:var(--grey)}
.legend i{display:inline-block;width:3px;height:3px;margin-right:1px;vertical-align:middle}

/* pie labels */
.pie-label{position:absolute;width:60px}
.pie-label h4{font-size:4.2px;font-weight:700;color:var(--ink);margin-bottom:2px}
.pie-label.hl h4{color:var(--orange)}
.pie-label.dim h4{color:#b5b5b5}

/* table */
.table{position:absolute;left:12px;top:62px;width:219px;border-collapse:collapse;font-size:4.6px}
.table th{font-weight:400;color:var(--grey);font-size:3.6px;height:12px;border-top:1px solid #d0d0d0}
.table td{height:19px;text-align:center;color:var(--grey)}
.table td.type{text-align:left;padding-left:22px;font-size:3.6px}
.table tr.dark td{background:var(--ink);color:var(--white)}

/* team */
.member{position:absolute;top:42px;width:68px}
.member .portrait{width:66px;height:40px;border:1.5px solid var(--orange)}
.member h5{font-size:4.2px;color:var(--ink);margin-top:3px}
.member .role{font-size:3px;color:var(--mid);margin-bottom:3px}
.member .copy{border-top:1px solid #d8d8d8;border-bottom:1px solid #d8d8d8;padding:3px 0;text-align:left}

/* stats */
.stat{position:absolute;width:82px;height:42px;padding:5px 4px 0 20px}
.stat.orange{background:var(--orange)}
.stat.grey{background:#5d5d5d}
.stat.dark{background:#141414}
.stat .num{font-size:8.5px;font-weight:400;color:var(--white)}
.stat .copy{color:var(--white);font-size:3.2px;line-height:1.35;text-align:left;margin-top:2px}
.stat-icon{position:absolute;width:18px;height:18px;border-radius:50%;left:-9px;top:12px;border:1px solid var(--white)}

/* thank you */
.thanks{position:absolute;left:20px;top:26px;font-size:26px;font-weight:300;line-height:1.08;color:var(--white)}
.end-brand{right:12px;bottom:22px;font-size:13px}
.end-brand .brand-dot{width:13px;height:13px}
</style>
</head>
<body>
<main class="board">
  <div class="divider-v" style="left:299px"></div>
  <div class="divider-v" style="left:599px"></div>
  <div class="divider-v" style="left:899px"></div>
  <div class="divider-h" style="top:240px"></div>
  <div class="divider-h" style="top:481px"></div>

  <div class="page-label c1" style="top:18px">Page 1</div>
  <div class="page-label c2" style="top:18px">Page 2</div>
  <div class="page-label c3" style="top:18px">Page 3</div>
  <div class="page-label c4" style="top:18px">Page 4</div>
  <div class="page-label c1" style="top:259px">Page 5</div>
  <div class="page-label c2" style="top:259px">Page 6</div>
  <div class="page-label c3" style="top:259px">Page 7</div>
  <div class="page-label c4" style="top:259px">Page 8</div>
  <div class="page-label c1" style="top:499px">Page 9</div>
  <div class="page-label c2" style="top:499px">Page 10</div>
  <div class="page-label c3" style="top:499px">Page 11</div>
  <div class="page-label c4" style="top:499px">Page 12</div>

  <!-- Title slide -->
  <section class="slide c1 r1 slide-title">
    <svg class="photo" width="243" height="182" viewBox="0 0 243 182" role="img" aria-label="Photo of a hand typing on a laptop keyboard">
      <defs><linearGradient id="kb" x1="0" y1="0" x2="1" y2="1"><stop offset="0" stop-color="#a8a39c"/><stop offset=".55" stop-color="#4b4944"/><stop offset="1" stop-color="#1e1e1e"/></linearGradient></defs>
      <polygon points="168,0 243,0 243,182 42,182" fill="url(#kb)"/>
    </svg>
    <svg class="abs" width="243" height="182" viewBox="0 0 243 182">
      <polygon points="160,0 172,0 46,182 34,182" fill="#1f2633"/>
      <polygon points="174,0 184,0 62,182 52,182" fill="#f78f20"/>
      <polygon points="205,0 243,0 243,6 221,22 190,22" fill="#f78f20"/>
      <polygon points="228,0 243,0 243,8 232,8" fill="#1f2633"/>
      <polygon points="0,168 20,155 30,155 8,182 0,182" fill="#f78f20"/>
      <polygon points="12,182 32,160 40,160 22,182" fill="#1f2633"/>
    </svg>
    <div class="brand title-brand"><span class="brand-dot"></span>Bold Ledger</div>
    <div class="tagline"><div class="accent">interactive digital platform</div><div class="plain">to share actionable advice</div></div>
  </section>

  <!-- Transition -->
  <section class="slide c2 r1">
    <svg class="photo" width="243" height="182" viewBox="0 0 243 182" role="img" aria-label="Photo of hands holding a smartphone with glowing app icons">
      <defs><radialGradient id="phone" cx=".55" cy=".4" r=".75"><stop offset="0" stop-color="#6fb6e6"/><stop offset=".5" stop-color="#1d5d8e"/><stop offset="1" stop-color="#0a1f35"/></radialGradient></defs>
      <rect width="243" height="182" fill="url(#phone)"/>
    </svg>
    <svg class="abs" width="243" height="182" viewBox="0 0 243 182">
      <polygon points="92,145 243,145 243,182 68,182" fill="#111a28" opacity=".92"/>
      <polygon points="76,145 88,145 64,182 52,182" fill="#f78f20"/>
    </svg>
    <div class="transition-title">Transition Page</div>
  </section>

  <!-- About text + photo -->
  <section class="slide c3 r1">
    <div class="head"><div class="head-orange"></div><div class="head-dark"></div><div class="head-line"></div><span class="head-title">About Our Company</span><div class="brand"><span class="brand-dot"></span>Bold Ledger</div></div>
    <div class="abs" style="left:9px;top:41px;width:110px">
      <p class="lead">Leaders share real lessons here, and every idea is written to be used the same week by busy teams.</p>
      <p class="copy" style="margin-top:4px">Our platform gives executives a calm place to trade practical advice. Members post short notes, answer questions and rate the tips that helped. Each thread stays focused on one decision, so readers find what they need fast. Good advice rises to the top through votes from peers who face the same choices. Teams can follow topics, save answers and share them with staff in a single step. Weekly digests bring the best threads to every inbox.</p>
      <p class="copy" style="margin-top:4px">Start with one question and let the network do the rest.</p>
    </div>
    <div class="abs" style="left:126px;top:41px;width:108px">
      <p class="copy">We built this space for people who lead. It values clear thinking, honest results and quick follow up over noise and long debates.</p>
    </div>
    <svg class="photo" style="left:126px;top:80px" width="106" height="63" role="img" aria-label="Photo of a businessman in a suit holding a tablet with floating icons"><defs><linearGradient id="biz" x1="0" y1="0" x2="0" y2="1"><stop offset="0" stop-color="#3a3f47"/><stop offset="1" stop-color="#0f1114"/></linearGradient></defs><rect width="106" height="63" fill="url(#biz)"/></svg>
    <div class="foot"><div class="foot-band"></div><span class="foot-text">www.boldledger.com | Page 1</span></div>
  </section>

  <!-- Image + bullets -->
  <section class="slide c4 r1">
    <div class="head"><div class="head-orange"></div><div class="head-dark"></div><div class="head-line"></div><span class="head-title">Title Goes Here</span><div class="brand"><span class="brand-dot"></span>Bold Ledger</div></div>
    <svg class="photo" style="left:20px;top:46px" width="80" height="52" role="img" aria-label="Illustration of a laptop surrounded by colourful app icons"><defs><radialGradient id="lap" cx=".5" cy=".5" r=".6"><stop offset="0" stop-color="#5aa7e0"/><stop offset=".7" stop-color="#b9d7ee"/><stop offset="1" stop-color="#f4f4f4"/></radialGradient></defs><rect width="80" height="52" fill="url(#lap)"/></svg>
    <p class="copy abs" style="left:12px;top:106px;width:108px">Post a question, gather answers from peers and keep the best ideas in one place. Every thread is short, useful and easy to share with your team.</p>
    <ul class="bullets">
      <li>Share one clear lesson from this quarter.</li>
      <li>Ask peers how they handled the same choice.</li>
      <li>Rate the advice that made a real difference.</li>
      <li>Save strong answers for your next meeting.</li>
      <li>Invite your team to follow key topics.</li>
    </ul>
    <div class="foot"><div class="foot-band"></div><span class="foot-text">www.boldledger.com | Page 2</span></div>
  </section>

  <!-- Three features -->
  <section class="slide c1 r2">
    <div class="head"><div class="head-orange"></div><div class="head-dark"></div><div class="head-line"></div><span class="head-title">About Our Company</span><div class="brand"><span class="brand-dot"></span>Bold Ledger</div></div>
    <div class="feature" style="left:12px">
      <svg width="22" height="20" viewBox="0 0 22 20"><rect x="2" y="1" width="18" height="13" fill="none" stroke="#1f2633" stroke-width="1.6"/><polyline points="5,11 9,7 12,9 17,4" fill="none" stroke="#1f2633" stroke-width="1.2"/><rect x="0" y="15" width="22" height="2" fill="#1f2633"/></svg>
      <p class="copy">Track the advice you use and see which ideas move results for your teams over time.</p>
    </div>
    <div class="feature" style="left:90px">
      <svg width="24" height="20" viewBox="0 0 24 20"><circle cx="8" cy="10" r="6" fill="none" stroke="#f78f20" stroke-width="1.6"/><circle cx="16" cy="10" r="6" fill="none" stroke="#f78f20" stroke-width="1.6"/></svg>
      <p class="copy">Connect with leaders who faced the same problem and learn from the path they chose.</p>
    </div>
    <div class="feature" style="left:168px">
      <svg width="22" height="20" viewBox="0 0 22 20"><rect x="2" y="9" width="4" height="9" fill="none" stroke="#1f2633" stroke-width="1.4"/><path d="M7 9 L11 2 Q13 1 13 4 L12 8 L19 8 Q20 9 19 11 L17 18 L7 18 Z" fill="none" stroke="#1f2633" stroke-width="1.4"/></svg>
      <p class="copy">Vote for the tips that worked so the most useful answers reach every member first.</p>
    </div>
    <div class="foot"><div class="foot-band"></div><span class="foot-text">www.boldledger.com | Page 3</span></div>
  </section>

  <!-- Bar chart -->
  <section class="slide c2 r2">
    <div class="head"><div class="head-orange"></div><div class="head-dark"></div><div class="head-line"></div><span class="head-title">About Our Company</span><div class="brand"><span class="brand-dot"></span>Bold Ledger</div></div>
    <svg class="abs" style="left:8px;top:50px" width="200" height="80" viewBox="0 0 200 80" font-family="Lato, sans-serif" font-size="3.6" fill="#757575">
      <g stroke="#e0e0e0" stroke-width=".4"><line x1="12" y1="4" x2="200" y2="4"/><line x1="12" y1="16.4" x2="200" y2="16.4"/><line x1="12" y1="28.8" x2="200" y2="28.8"/><line x1="12" y1="41.2" x2="200" y2="41.2"/><line x1="12" y1="53.6" x2="200" y2="53.6"/></g>
      <line x1="12" y1="66" x2="200" y2="66" stroke="#bbb" stroke-width=".5"/>
      <text x="6" y="5">5</text><text x="6" y="17.4">4</text><text x="6" y="29.8">3</text><text x="6" y="42.2">2</text><text x="6" y="54.6">1</text><text x="6" y="67">0</text>
      <rect x="24" y="12" width="11" height="54" fill="#f78f20"/><rect x="35" y="36" width="11" height="30" fill="#1f2633"/><rect x="46" y="15" width="11" height="51" fill="#8a8a8a"/>
      <rect x="86" y="21" width="11" height="45" fill="#f78f20"/><rect x="97" y="10" width="11" height="56" fill="#1f2633"/><rect x="108" y="33" width="11" height="33" fill="#8a8a8a"/>
      <rect x="148" y="16" width="11" height="50" fill="#f78f20"/><rect x="159" y="14" width="11" height="52" fill="#1f2633"/><rect x="170" y="6" width="11" height="60" fill="#8a8a8a"/>
      <text x="33" y="73">Category 1</text><text x="96" y="73">Category 2</text><text x="157" y="73">Category 3</text>
    </svg>
    <div class="legend" style="left:212px;top:50px"><div><i style="background:#f78f20"></i>Series 1</div><div><i style="background:#1f2633"></i>Series 2</div><div><i style="background:#8a8a8a"></i>Series 3</div></div>
    <p class="copy abs" style="left:14px;top:134px;width:216px">Replace the sample values with your own figures. Each series keeps its colour so comparisons stay clear across every category and slide in the deck.</p>
    <div class="foot"><div class="foot-band"></div><span class="foot-text">www.boldledger.com | Page 4</span></div>
  </section>

  <!-- Area chart -->
  <section class="slide c3 r2">
    <div class="head"><div class="head-orange"></div><div class="head-dark"></div><div class="head-line"></div><span class="head-title">About Our Company</span><div class="brand"><span class="brand-dot"></span>Bold Ledger</div></div>
    <svg class="abs" style="left:8px;top:50px" width="210" height="76" viewBox="0 0 210 76" font-family="Lato, sans-serif" font-size="3.6" fill="#757575">
      <g stroke="#e0e0e0" stroke-width=".4"><line x1="12" y1="4" x2="204" y2="4"/><line x1="12" y1="15" x2="204" y2="15"/><line x1="12" y1="26" x2="204" y2="26"/><line x1="12" y1="37" x2="204" y2="37"/><line x1="12" y1="48" x2="204" y2="48"/></g>
      <text x="6" y="5">5</text><text x="6" y="16">4</text><text x="6" y="27">3</text><text x="6" y="38">2</text><text x="6" y="49">1</text><text x="6" y="60">0</text>
      <polygon points="14,38 120,14 210,4 210,59 14,59" fill="#1f2633"/>
      <polygon points="14,38 92,8 150,32 210,24 210,59 14,59" fill="#f78f20"/>
      <polygon points="14,45 120,32 210,26 210,59 14,59" fill="#a5a5a5"/>
      <text x="14" y="66">Category 1</text><text x="104" y="66">Category 2</text><text x="190" y="66">Category 3</text>
    </svg>
    <div class="legend" style="left:214px;top:50px"><div><i style="background:#1f2633"></i>Series 1</div><div><i style="background:#f78f20"></i>Series 2</div><div><i style="background:#a5a5a5"></i>Series 3</div></div>
    <p class="copy abs" style="left:14px;top:128px;width:216px">Use this area chart to show growth over time. Swap in your data and the layers update while the shapes, colours and labels remain neat and easy to read.</p>
    <div class="foot"><div class="foot-band"></div><span class="foot-text">www.boldledger.com | Page 5</span></div>
  </section>

  <!-- Pie chart -->
  <section class="slide c4 r2">
    <div class="head"><div class="head-orange"></div><div class="head-dark"></div><div class="head-line"></div><span class="head-title">About Our Company</span><div class="brand"><span class="brand-dot"></span>Bold Ledger</div></div>
    <svg class="abs" style="left:0;top:40px" width="243" height="130" viewBox="0 0 243 130" font-family="Lato, sans-serif" font-size="4" fill="#ffffff">
      <g stroke="#bbb" stroke-width=".4" fill="none"><polyline points="20,41 84,41 108,56"/><polyline points="223,41 160,41 136,56"/><polyline points="20,85 84,85 108,76"/><polyline points="223,85 160,85 136,76"/></g>
      <path d="M122 42 A24 24 0 0 1 146 66 L134 66 A12 12 0 0 0 122 54 Z" fill="#f78f20"/>
      <path d="M146 66 A24 24 0 0 1 122 90 L122 78 A12 12 0 0 0 134 66 Z" fill="#c9c9c9"/>
      <path d="M122 90 A24 24 0 0 1 98 66 L110 66 A12 12 0 0 0 122 78 Z" fill="#1f2633"/>
      <path d="M98 66 A24 24 0 0 1 122 42 L122 54 A12 12 0 0 0 110 66 Z" fill="#3b4250"/>
      <text x="105" y="62">25%</text><text x="132" y="62">25%</text><text x="105" y="75">25%</text><text x="132" y="75">25%</text>
    </svg>
    <div class="pie-label" style="left:20px;top:68px"><h4>NOBIS VIDENTUR</h4><p class="copy" style="text-align:left">Short note on this share of the total result.</p></div>
    <div class="pie-label hl" style="left:160px;top:68px"><h4>NOBIS VIDENTUR</h4><p class="copy" style="text-align:left">Short note on this share of the total result.</p></div>
    <div class="pie-label" style="left:20px;top:117px"><h4>NOBIS VIDENTUR</h4><p class="copy" style="text-align:left">Short note on this share of the total result.</p></div>
    <div class="pie-label dim" style="left:160px;top:117px"><h4>NOBIS VIDENTUR</h4><p class="copy" style="text-align:left">Short note on this share of the total result.</p></div>
    <div class="foot"><div class="foot-band"></div><span class="foot-text">www.boldledger.com | Page 6</span></div>
  </section>

  <!-- Table -->
  <section class="slide c1 r3">
    <div class="head"><div class="head-orange"></div><div class="head-dark"></div><div class="head-line"></div><span class="head-title">About Our Company</span><div class="brand"><span class="brand-dot"></span>Bold Ledger</div></div>
    <table class="table">
      <thead><tr><th></th><th>A</th><th>B</th><th>C</th></tr></thead>
      <tbody>
        <tr class="dark"><td class="type">Type 1</td><td>20</td><td>30</td><td>40</td></tr>
        <tr><td class="type">Type 2</td><td>50</td><td>60</td><td>70</td></tr>
        <tr class="dark"><td class="type">Type 3</td><td>80</td><td>90</td><td>100</td></tr>
      </tbody>
    </table>
    <div class="foot"><div class="foot-band"></div><span class="foot-text">www.boldledger.com | Page 7</span></div>
  </section>

  <!-- Team -->
  <section class="slide c2 r3">
    <div class="head"><div class="head-orange"></div><div class="head-dark"></div><div class="head-line"></div><span class="head-title">About Our Company</span><div class="brand"><span class="brand-dot"></span>Bold Ledger</div></div>
    <div class="member" style="left:10px">
      <svg class="portrait" role="img" aria-label="Portrait photo of a team member"><defs><linearGradient id="p1" x1="0" y1="0" x2="1" y2="1"><stop offset="0" stop-color="#dfe6ec"/><stop offset="1" stop-color="#7f8a95"/></linearGradient></defs><rect width="100%" height="100%" fill="url(#p1)"/></svg>
      <h5>Mr A. Carter</h5><div class="role">(President)</div>
      <p class="copy">Leads strategy and partner growth with a focus on clear, useful advice for every member.</p>
    </div>
    <div class="member" style="left:88px">
      <svg class="portrait" role="img" aria-label="Portrait photo of a team member"><defs><linearGradient id="p2" x1="0" y1="0" x2="1" y2="1"><stop offset="0" stop-color="#e4e4e4"/><stop offset="1" stop-color="#5c5f66"/></linearGradient></defs><rect width="100%" height="100%" fill="url(#p2)"/></svg>
      <h5>Mr A. Carter</h5><div class="role">(President)</div>
      <p class="copy">Leads strategy and partner growth with a focus on clear, useful advice for every member.</p>
    </div>
    <div class="member" style="left:166px">
      <svg class="portrait" role="img" aria-label="Portrait photo of a team member outdoors"><defs><linearGradient id="p3" x1="0" y1="0" x2="1" y2="1"><stop offset="0" stop-color="#b9b89a"/><stop offset="1" stop-color="#6a6655"/></linearGradient></defs><rect width="100%" height="100%" fill="url(#p3)"/></svg>
      <h5>Mr A. Carter</h5><div class="role">(President)</div>
      <p class="copy">Leads strategy and partner growth with a focus on clear, useful advice for every member.</p>
    </div>
    <div class="foot"><div class="foot-band"></div><span class="foot-text">www.boldledger.com | Page 8</span></div>
  </section>

  <!-- Stats -->
  <section class="slide c3 r3">
    <div class="head"><div class="head-orange"></div><div class="head-dark"></div><div class="head-line"></div><span class="head-title">About Our Company</span><div class="brand"><span class="brand-dot"></span>Bold Ledger</div></div>
    <div class="stat orange" style="left:26px;top:48px">
      <span class="stat-icon" style="background:var(--orange)"><svg width="16" height="16" viewBox="0 0 16 16"><path d="M4 7 L9 4 L9 12 L4 9 Z M3 7 L4 7 L4 9 L3 9 Z" fill="none" stroke="#fff" stroke-width=".9"/></svg></span>
      <div class="num">915,456,459</div><p class="copy">Short line about this number and why it matters to members.</p>
    </div>
    <div class="stat grey" style="left:146px;top:48px">
      <span class="stat-icon" style="background:#5d5d5d"><svg width="16" height="16" viewBox="0 0 16 16"><circle cx="8" cy="9" r="4" fill="none" stroke="#fff" stroke-width=".9"/><text x="6.3" y="10.6" font-size="5" fill="#fff" font-family="Lato, sans-serif">$</text></svg></span>
      <div class="num">111,458,564</div><p class="copy">Short line about this number and why it matters to members.</p>
    </div>
    <div class="stat dark" style="left:26px;top:108px">
      <span class="stat-icon" style="background:#141414"><svg width="16" height="16" viewBox="0 0 16 16"><ellipse cx="8" cy="9" rx="4.5" ry="3.3" fill="#fff"/></svg></span>
      <div class="num">100%</div><p class="copy">Short line about this number and why it matters to members.</p>
    </div>
    <div class="stat dark" style="left:146px;top:108px">
      <span class="stat-icon" style="background:#141414"><svg width="16" height="16" viewBox="0 0 16 16"><rect x="4" y="9" width="2" height="3" fill="#fff"/><rect x="7" y="7" width="2" height="5" fill="#fff"/><rect x="10" y="5" width="2" height="7" fill="#fff"/></svg></span>
      <div class="num">100%</div><p class="copy">Short line about this number and why it matters to members.</p>
    </div>
    <div class="foot"><div class="foot-band"></div><span class="foot-text">www.boldledger.com | Page 9</span></div>
  </section>

  <!-- Thank you -->
  <section class="slide c4 r3" style="background:var(--white)">
    <svg class="abs" width="243" height="182" viewBox="0 0 243 182">
      <polygon points="0,0 236,0 36,182 0,182" fill="#f78f20"/>
      <polygon points="236,0 243,0 243,10 44,182 36,182" fill="#1f2633"/>
      <polygon points="222,0 230,0 28,182 20,182" fill="#ffffff" opacity=".35"/>
      <polygon points="0,130 26,150 40,182 0,182" fill="#1f2633"/>
      <polygon points="0,122 8,122 36,182 28,182" fill="#f78f20"/>
    </svg>
    <div class="thanks">THANK<br>YOU</div>
    <div class="brand end-brand"><span class="brand-dot"></span>Bold Ledger</div>
  </section>
</main>
</body>
</html>
```